Brivolt Technologies business card design

We need a business card designed with our new logo. it would be great if the card could communicate it is a technology based company.

Target Market(s)

system integrators

Industry/Entity Type

technology, IOT

Contact Information for Business Card

Name, designation, Address, telephone number, email address

Requirements
Must have
• logo and company name
Nice to have
• something to do with technology

```html
<!DOCTYPE html>
<html lang="en">
<head>
<meta charset="utf-8">
<title>Brivolt Technologies – Business Card</title>
<link rel="stylesheet" href="https://fonts.googleapis.com/css2?family=Arimo:ital,wght@0,400;0,700;1,400&display=swap">
<style>
  :root {
    --stage: #1c1c1d;
    --card: #333334;
    --card-pattern-a: #2d2d2e;
    --card-pattern-b: #3a3a3b;
    --accent: #f7931e;
    --ink: #ffffff;
    --ink-soft: #e6e6e6;
  }
  * { box-sizing: border-box; margin: 0; padding: 0; }
  html, body {
    width: 1200px; height: 900px; overflow: hidden;
    background: var(--stage);
    font-family: "Arimo", Arial, sans-serif;
  }
  .stage {
    position: relative; width: 1200px; height: 900px;
  }
  .card {
    position: absolute; left: 320px;
    width: 560px; height: 320px;
    background: var(--card);
    border-radius: 18px;
    overflow: hidden;
    box-shadow: 0 18px 40px rgba(0,0,0,.45);
  }
  .card--front { top: 90px; }
  .card--back { top: 470px; }

  .card__edge {
    position: absolute; left: 0; right: 0; bottom: 0;
    height: 8px; background: var(--accent);
  }

  .brand {
    display: flex; align-items: center; gap: 10px;
    color: var(--ink); font-weight: 700;
    letter-spacing: .5px;
  }
  .brand__mark {
    width: 14px; height: 14px; background: var(--accent);
  }
  .card--front .brand {
    position: absolute; top: 48px; right: 40px;
    font-size: 28px;
  }

  .person {
    position: absolute; left: 40px; top: 130px; width: 250px;
    text-align: right;
  }
  .person__name {
    color: var(--accent); font-size: 24px; font-weight: 700;
    letter-spacing: .5px; text-transform: uppercase;
  }
  .person__role {
    color: var(--ink-soft); font-size: 14px; font-style: italic;
    margin-top: 6px;
  }

  .divider {
    position: absolute; left: 310px; top: 138px;
    width: 1px; height: 78px; background: var(--accent);
  }

  .contacts {
    position: absolute; left: 330px; top: 140px;
    list-style: none;
  }
  .contacts li {
    display: flex; align-items: center; gap: 8px;
    color: var(--ink-soft); font-size: 14px; line-height: 26px;
  }
  .contacts svg { width: 13px; height: 13px; flex: none; }

  .address {
    position: absolute; left: 40px; bottom: 42px;
    color: var(--ink-soft); font-size: 14px;
  }

  .card__pattern {
    position: absolute; inset: 0;
    background: linear-gradient(135deg, var(--card-pattern-a), var(--card-pattern-b) 60%, var(--card-pattern-a));
  }
  .card--back .brand {
    position: absolute; left: 44px; bottom: 48px;
    font-size: 26px;
  }
</style>
</head>
<body>
<main class="stage">

  <section class="card card--front" aria-label="Business card front">
    <div class="brand"><span class="brand__mark"></span>Brivolt Technologies</div>

    <div class="person">
      <h1 class="person__name">Daniel Ostrander</h1>
      <p class="person__role">CEO/Founder</p>
    </div>

    <div class="divider"></div>

    <ul class="contacts">
      <li>
        <svg viewBox="0 0 24 24" fill="var(--accent)"><path d="M6.6 10.8a15 15 0 0 0 6.6 6.6l2.2-2.2c.3-.3.7-.4 1-.2 1.1.4 2.3.6 3.6.6.6 0 1 .4 1 1V20c0 .6-.4 1-1 1A17 17 0 0 1 3 4c0-.6.4-1 1-1h3.5c.6 0 1 .4 1 1 0 1.3.2 2.5.6 3.6.1.3 0 .7-.2 1z"/></svg>
        (555) 014-2290
      </li>
      <li>
        <svg viewBox="0 0 24 24" fill="var(--accent)"><path d="M2 5h20v14H2z" opacity=".9"/><path d="M2 5l10 8 10-8" fill="none" stroke="var(--card)" stroke-width="2"/></svg>
        info@brivolttech.com
      </li>
      <li>
        <svg viewBox="0 0 24 24" fill="none" stroke="var(--accent)" stroke-width="2"><circle cx="12" cy="12" r="10"/><path d="M2 12h20M12 2c3 3 3 17 0 20M12 2c-3 3-3 17 0 20"/></svg>
        www.brivolttech.com
      </li>
    </ul>

    <p class="address">1820 Harbor Lane Westfield AB 4417</p>

    <div class="card__edge"></div>
  </section>

  <section class="card card--back" aria-label="Business card back">
    <div class="card__pattern" role="img" aria-label="Tonal repeating brand-mark pattern across the card back"></div>
    <div class="brand"><span class="brand__mark"></span>Brivolt Technologies</div>
  </section>

</main>
</body>
</html>
```